Executive Taxi firm with Chauffeur service Website

I have my domain name registered and I have started to work on my site but I am struggling. I am just about to get a logo for the company and need a web site that clearly represents the fact we are an executive/luxury brand in private hire vehicles. We offer airport transfers, train station transfers, seaport transfers, holiday transfers and business to business pick up and drop off.

Target Market(s)

Corporate people, holidaymakers looking for a luxury start their holiday. VIPs' and celebrities.

Number of Pages Required

5+ page

Font styles to use
Serif
Sans Serif
Decorative
Script

Colors

Designer to choose colors to be used in the design.

Requirements
Must have
• Home Page, Services, About Us, VIP and Contact us
• Please see www.brivomotors.co.uk I have started it but not happy with it at all.
Nice to have
• Booking form or enquiry form.

```html
<!DOCTYPE html>
<html lang="en">
<head>
<meta charset="utf-8">
<title>Brivo Motors – Executive Travel</title>
<link href="https://fonts.googleapis.com/css2?family=Poppins:wght@400;500;600;700&family=Open+Sans:wght@400;600&display=swap" rel="stylesheet">
<style>
:root{
  --yellow:#f5b819;
  --yellow-dark:#e0a40a;
  --ink:#222428;
  --text:#555a60;
  --muted:#8a8f95;
  --white:#ffffff;
  --night:#15171b;
  --line:#d9d9d9;
}
*{box-sizing:border-box;margin:0;padding:0}
html,body{width:1200px;height:4000px;overflow:hidden}
body{position:relative;font-family:"Open Sans",Arial,sans-serif;color:var(--text);background:var(--white)}
h1,h2,h3,.brand,.nav,.btn{font-family:"Poppins",Arial,sans-serif}
.abs{position:absolute}
.btn{display:inline-block;background:var(--yellow);color:var(--white);font-size:15px;font-weight:500;padding:10px 26px;border-radius:3px}
.btn-small{font-size:11px;padding:5px 14px}
.brand{display:flex;align-items:center;gap:12px;font-weight:700;font-size:30px}
.brand-dot{width:40px;height:40px;border-radius:50%;background:var(--yellow)}

/* hero */
.hero{left:0;top:0;width:1200px;height:680px;background:linear-gradient(180deg,#2b2d31 0%,#3a3c40 45%,#1c1d20 100%)}
.hero .brand{left:90px;top:36px;color:var(--white)}
.nav{right:90px;top:48px;display:flex;align-items:center;gap:36px;font-size:15px;color:var(--white)}
.nav .active{color:var(--yellow)}
.nav-phone{width:36px;height:36px;border:2px solid var(--white);border-radius:50%;display:flex;align-items:center;justify-content:center}
.hero-sub{top:215px;width:1200px;text-align:center;color:var(--white);font-size:34px;font-weight:500}
.hero-title{top:270px;width:1200px;text-align:center;color:var(--white);font-size:44px;font-weight:700}
.hero-cta{top:355px;left:510px;width:180px;height:50px;border:2px solid var(--yellow);color:var(--white);font-family:"Poppins",sans-serif;font-size:17px;display:flex;align-items:center;justify-content:center}
.car{left:260px;top:500px;width:640px;height:300px;border-radius:140px 160px 40px 40px;background:radial-gradient(ellipse at 50% 40%,#ffd93a 0%,#f2c100 55%,#b98f00 100%)}

/* about */
.about-label{left:90px;top:895px;font-family:"Poppins",sans-serif;font-size:40px;color:var(--yellow);font-weight:500}
.about-title{left:90px;top:945px;font-size:50px;color:var(--ink);font-weight:600}
.about-text{left:90px;top:1030px;width:620px;font-size:13px;line-height:2}
.about-text p+p{margin-top:14px}
.about-btn{left:90px;top:1235px}
.booking{left:740px;top:855px;width:370px;height:450px;background:var(--white);box-shadow:0 4px 18px rgba(0,0,0,.18)}
.booking h3{background:var(--yellow);color:var(--ink);font-size:22px;font-weight:500;text-align:center;padding:14px 0}
.field{margin:0 38px;border-bottom:1px solid var(--line);height:46px;display:flex;align-items:flex-end;padding-bottom:6px;font-size:13px;color:var(--ink)}
.booking .submit{display:block;margin:26px auto 0;width:290px;text-align:center;background:var(--yellow);color:var(--ink);font-size:20px;padding:9px 0}

/* services */
.services{left:0;top:1420px;width:1200px;height:720px;background:linear-gradient(135deg,#f7c230 0%,#f0ad0a 60%,#e49a05 100%)}
.services h2{position:absolute;top:110px;width:1200px;text-align:center;color:var(--white);font-size:46px;font-weight:500}
.card{top:200px;width:330px;height:420px;background:var(--white)}
.card-photo{height:200px}
.card h3{font-size:18px;font-weight:600;color:var(--ink);text-align:center;margin:20px 0 10px}
.card p{font-size:12px;line-height:1.7;text-align:center;padding:0 26px}
.card .btn{position:absolute;bottom:28px;left:50%;transform:translateX(-50%)}

/* always here */
.phone-scene{left:140px;top:2270px;width:300px;height:620px;border-radius:40px 40px 0 0;background:linear-gradient(160deg,#f1ddc7 0%,#dcbfa1 60%,#c9a584 100%)}
.always-title{left:495px;top:2305px;font-size:50px;color:var(--ink);font-weight:500}
.always-text{left:495px;top:2410px;width:610px;font-size:12.5px;line-height:1.95}
.always-text p+p{margin-top:14px}
.always-btn{left:495px;top:2700px}

/* testimonials */
.testimonials{left:0;top:2910px;width:1200px;height:530px;background:linear-gradient(180deg,#26282c 0%,#1a1b1e 40%,#3a2a12 100%)}
.testimonials h2{position:absolute;top:70px;width:1200px;text-align:center;color:var(--white);font-size:46px;font-weight:500}
.review{top:190px;width:440px;height:220px;background:var(--white);padding:36px 30px 0 150px}
.avatar{position:absolute;left:28px;top:44px;width:100px;height:100px;border-radius:50%;background:linear-gradient(135deg,#d8b79a,#9e7a5c)}
.quote{position:absolute;right:28px;top:20px;font-family:"Poppins",sans-serif;font-size:70px;color:var(--yellow);line-height:1}
.review p{font-size:14px;line-height:1.6;margin-top:24px;padding-right:40px}
.stars{margin-top:14px;color:var(--yellow);font-size:14px;letter-spacing:2px}
.review .name{position:absolute;right:30px;bottom:30px;font-size:13px;color:var(--yellow)}
.dots{top:3398px;left:580px;display:flex;gap:8px}
.dots span{width:8px;height:8px;border-radius:50%;background:#777}
.dots span:first-child{background:var(--white)}

/* newsletter & footer */
.news-label{left:270px;top:3547px;font-family:"Poppins",sans-serif;font-size:24px;color:var(--ink);font-weight:500}
.news-input{left:440px;top:3540px;width:360px;height:44px;border:1px solid var(--line);border-radius:22px 0 0 22px;padding:12px 20px;font-size:12px;color:var(--muted)}
.news-btn{left:800px;top:3540px;width:120px;height:44px;background:var(--yellow);color:var(--white);font-size:12px;border-radius:0 22px 22px 0;display:flex;align-items:center;justify-content:center;font-family:"Poppins",sans-serif;font-weight:600}
.footer-rule{left:90px;top:3640px;width:1020px;height:1px;background:var(--line)}
.footer .brand{left:130px;top:3760px;color:var(--ink)}
.col{top:3710px;font-size:12px;line-height:1.9}
.col h4{font-family:"Poppins",sans-serif;font-size:13px;color:var(--ink);font-weight:600;margin-bottom:12px}
.col li{list-style:none}
.col li::before{content:"› ";color:var(--yellow)}
.socials{display:flex;gap:10px}
.socials span{width:26px;height:26px;background:var(--ink);border-radius:3px}
.copyright{left:0;top:3945px;width:1200px;height:55px;background:#f2f2f2;text-align:center;line-height:55px;font-size:12px;color:var(--text)}
</style>
</head>
<body>

<header class="abs hero" role="img" aria-label="Dark night photo of a chauffeur beside an executive car"></header>
<div class="abs brand" style="left:90px;top:36px;color:var(--white)"><span class="brand-dot"></span>Brivo Motors</div>
<nav class="abs nav">
  <span class="active">Home</span><span>Services</span><span>About Us</span><span>VIP</span><span>Contact Us</span>
  <span class="nav-phone"><svg width="16" height="16" viewBox="0 0 24 24" fill="#fff"><path d="M6.6 10.8a15 15 0 0 0 6.6 6.6l2.2-2.2c.3-.3.7-.4 1-.2 1.1.4 2.3.6 3.6.6.6 0 1 .4 1 1V20c0 .6-.4 1-1 1A17 17 0 0 1 3 4c0-.6.4-1 1-1h3.5c.6 0 1 .4 1 1 0 1.3.2 2.5.6 3.6.1.3 0 .7-.2 1z"/></svg></span>
</nav>
<h1 class="abs hero-sub">Private Hire, Chauffeur and taxi service</h1>
<h1 class="abs hero-title">Executive Brivo Motors</h1>
<div class="abs hero-cta">BOOK NOW</div>
<div class="abs car" role="img" aria-label="Yellow executive taxi saloon"></div>

<section>
  <h2 class="abs about-label">About</h2>
  <h2 class="abs about-title">Brivo Motors</h2>
  <div class="abs about-text">
    <p>Brivo Motors offers a calm, private way to travel. Every journey is planned around you, with trained drivers, spotless executive cars and fixed fares agreed before you set off. We cover airports, stations, seaports and city meetings across the region, day and night, with a friendly team ready to help whenever plans change at short notice.</p>
    <p>Whether you are flying out on holiday or meeting a client, our chauffeurs arrive early, track your flight and help with luggage so you can relax from the first mile to the last.</p>
  </div>
  <span class="abs btn about-btn">Read More</span>
  <form class="abs booking">
    <h3>Book a Ride with Us</h3>
    <div class="field">First Name</div>
    <div class="field">Last Name</div>
    <div class="field">Email</div>
    <div class="field">Phone</div>
    <div class="field">Date</div>
    <div class="field">Time</div>
    <span class="btn submit">Submit</span>
  </form>
</section>

<section class="abs services">
  <h2>OUR SERVICES</h2>
  <article class="abs card" style="left:90px">
    <div class="card-photo" role="img" aria-label="Chauffeur opening a car door for a passenger" style="background:linear-gradient(135deg,#5a5f66,#2c2f33)"></div>
    <h3>Airport Transfers</h3>
    <p>Airport and seaport transfers are our speciality. Our drivers track your flight and wait in arrivals with your name.</p>
    <span class="btn btn-small">View Details</span>
  </article>
  <article class="abs card" style="left:435px">
    <div class="card-photo" role="img" aria-label="Business traveller stepping into an executive car" style="background:linear-gradient(135deg,#8a8e94,#3b3e43)"></div>
    <h3>Business to Business Transfers</h3>
    <p>For a stress free chauffeur service, travel with us between offices, hotels and meetings with comfort on every trip.</p>
    <span class="btn btn-small">View Details</span>
  </article>
  <article class="abs card" style="left:780px">
    <div class="card-photo" role="img" aria-label="Yellow taxi on a city street" style="background:linear-gradient(135deg,#f3c22a,#6b5a2a)"></div>
    <h3>Holiday Transfers</h3>
    <p>Start your holiday in style. We collect the whole family and luggage and drop you right at the terminal door.</p>
    <span class="btn btn-small">View Details</span>
  </article>
</section>

<section>
  <div class="abs phone-scene" role="img" aria-label="Hand holding a smartphone showing a ride booking map"></div>
  <h2 class="abs always-title">Always here for you</h2>
  <div class="abs always-text">
    <p>We provide airport transfers to and from all major UK airports, seaports and train stations, plus executive business to business transfers. Whether you are a single traveller or a group, our team will find the right vehicle, from luxury saloons to spacious people carriers, at a fare agreed in advance.</p>
    <p>We provide a door to door service from your home, office or hotel straight to any destination. Our drivers watch live traffic and flight times, and meet you with a name board on arrival. Pickups run day and night, seven days a week, so you can relax with us whenever your journey starts.</p>
  </div>
  <span class="abs btn always-btn">Read More</span>
</section>

<section class="abs testimonials" role="img" aria-label="Night city street with light trails">
  <h2>Testimonial</h2>
  <article class="abs review" style="left:130px">
    <span class="avatar" role="img" aria-label="Customer portrait"></span><span class="quote">“</span>
    <p>The ride was smooth, the driver was early and the car was spotless. I will book again.</p>
    <div class="stars">★★★★☆</div>
    <span class="name">Hannah Reed</span>
  </article>
  <article class="abs review" style="left:650px">
    <span class="avatar" role="img" aria-label="Customer portrait"></span><span class="quote">“</span>
    <p>Friendly chauffeur, comfortable car and a fair price. Our holiday started perfectly with them.</p>
    <div class="stars">★★★★☆</div>
    <span class="name">Laura Pike</span>
  </article>
</section>
<div class="abs dots"><span></span><span></span><span></span></div>

<section>
  <div class="abs news-label">NEWSLETTER</div>
  <div class="abs news-input">you@example.com</div>
  <div class="abs news-btn">SUBSCRIBE</div>
</section>

<footer class="footer">
  <div class="abs footer-rule"></div>
  <div class="abs brand" style="left:130px;top:3760px;color:var(--ink)"><span class="brand-dot"></span>Brivo Motors</div>
  <div class="abs col" style="left:390px">
    <h4>INFORMATION</h4>
    <ul><li>Privacy Policy</li><li>Your Account</li><li>Advanced Search</li><li>Contact Us</li></ul>
  </div>
  <div class="abs col" style="left:610px">
    <h4>CONTACT US</h4>
    <div>Address – 12 Harrow Lane,<br>Northgate NG4 2LX</div>
    <div>Phone – 01632 960 412</div>
    <div>Email – info@brivomotors.co.uk</div>
    <div>www.brivomotors.co.uk</div>
  </div>
  <div class="abs col" style="left:880px">
    <h4>FOLLOW US OUT THERE</h4>
    <div class="socials"><span></span><span></span><span></span><span></span></div>
  </div>
  <div class="abs copyright">Copyright © 2018. All Rights Reserved</div>
</footer>

</body>
</html>
```